Commercial Rooftop Solar business needs a website

We need a website with fantastic appeal for a new company based in Melbourne called Tallow Ridge Energy. We design and install solar energy systems for commercial applications across Australia. Our market is to focus on small to medium businesses looking for solar solutions, but we will also provide our service for residential customers. We would like a beautiful 'front page' feel to our home page, using photographs of solar PV systems and/or natural imagery. Our logo uses the colours orange and black, which could easily be echoed in photographic imagery of sunset and sunrise, for example. The design should communicate quiet confidence and professionalism to a corporate marketplace.

NEW POINTS FOR BRIEF: This design also needs to be flexible to allow for additional future content, including a Support page with sub pages, FAQ's, and a Blog.

As part of this design project, we will require the coding for the website to be completed by the designer.

We have seen some websites, which we like the look and feel of: these are listed below.

brightvanepower.com.au:

• Beautiful images underlaying brief text selling points.
• Simple ‘front cover’ style home page with elegant drop-down menu, stylish simple font style.
• Home page invites exploration through the menu links, rather than trying to provide all the information up front.
• Company logo and name in the top left hand corner, contact details accessible at top right hand, seems consistent in most sites.

kelpworks.com.au

rumbofield.com:
• Same element as the others is the front-page style home page with beautiful images underlying text.

We have a webpage that we started uploading content to. You can use some of the content there in your designs: www.tallowridgeenergy.com.au

Technical Specifications:
PAGES:

Home

About Us

Solutions - Commercial
- Residential

Products - Solar Panels - Vorla Heron, Vorla TELD, Vorla QB
- Solar Inverters - Kestamo, BrilQuill
- Monitoring systems - Dunmere Metrics
- Batteries - RW

- Datasheets have been provided for reference but if it's too much work, you can use generic text and we will provide content later.

Contact Us

FUTURE PAGES (Please consider in structure, where links could be placed):

Support

FAQ's

Blog.

We could provide some content for the Support page soon, but the Blog and FAQ's are future pages which we don't want highlighted in the design as we don't yet have content.

Phone: 1800 7 BIRCH
Email: sales@tallowridgeenergy.com.au

Currently, I do not have images and text available. Please
use placeholders in the meantime. The final text and images will be uploaded for the winner once a winning design has been selected.

Target Market(s)

Primary focus is on small to medium sized business owners. Those owners will have a house which may be suitable for solar so we want to cater to residential deeper in the website.

Industry/Entity Type

Solar Energy

Coding

Coded - Design and coding required

Number of Pages Required

5+ page

Colors
f78f20
0255a3

Requirements
Must have
• Logo as per attachments.
Nice to have
• Logo can have alternate colours Eg. White on Orange or Black etc. provided colour correct logo is shown somewhere eg. footer or contact page.
• In the active site, I'd like to have:
• Very slowly zooming images - barely perceptible.
• Title text that rolls into place
• Subtle movements
• See https://plumtally.com.au/ for example

```html
<!DOCTYPE html>
<html lang="en">
<head>
<meta charset="utf-8">
<title>Contact – Tallow Ridge Energy</title>
<link href="https://fonts.googleapis.com/css2?family=Michroma&family=Open+Sans:wght@400;600;700&display=swap" rel="stylesheet">
<style>
:root{
  --accent:#f03c14;
  --ink:#1e1e1e;
  --text:#333;
  --line:#cfcfcf;
  --footer:#161616;
  --footer-deep:#0b0b0b;
  --white:#fff;
}
*{box-sizing:border-box;margin:0;padding:0}
html,body{width:899px;height:1200px;overflow:hidden}
body{position:relative;background:var(--white);font-family:"Open Sans",sans-serif;color:var(--text)}
.abs{position:absolute}
.display{font-family:"Michroma",sans-serif;text-transform:uppercase;white-space:nowrap}

/* hero */
.hero{left:0;top:0;width:899px;height:341px;background:linear-gradient(100deg,#9fae8c 0%,#d8d8d6 22%,#ecebe9 45%,#e9e8e6 70%,#c9c6c2 85%,#e6e5e3 100%)}
.topbar{left:0;top:0;width:899px;height:102px;background:rgba(60,60,60,.55)}
.brand{left:122px;top:30px;display:flex;align-items:center;gap:8px;color:var(--white);font-weight:600;font-size:15px}
.brand .dot{width:16px;height:16px;border-radius:50%;background:var(--white)}
.phone-top{left:553px;top:16px;display:flex;align-items:center;gap:7px;color:var(--white);font-weight:600;font-size:12.5px}
.quote-btn{left:673px;top:15px;width:113px;height:23px;border:1px solid var(--white);border-radius:12px;background:var(--accent);color:var(--white);font-weight:600;font-size:11.5px;line-height:21px;padding-left:10px}
.nav{left:323px;top:63px;display:flex;gap:13px;font-size:8px;letter-spacing:.6px;color:var(--white)}
.nav .active{color:var(--accent)}

/* heading */
.page-heading{left:0;top:378px;width:899px;display:flex;justify-content:center;align-items:center;gap:9px}
.page-heading .rule{width:56px;height:1px;background:var(--ink)}
.page-title{font-size:17px;color:var(--ink);letter-spacing:1.5px;font-weight:400}
.intro{left:0;top:438px;width:899px;text-align:center;font-size:11.3px;color:var(--text)}

/* form */
.form-title{left:132px;top:486px;font-size:12.5px;letter-spacing:1.5px;color:var(--ink);font-weight:400}
.label{font-size:9.6px;color:var(--text)}
.field{border:1px solid var(--line);background:var(--white)}
.select{font-size:9.6px;padding-left:8px;line-height:27px;color:var(--text)}
.select svg{position:absolute;right:8px;top:10px}
.submit{left:130px;top:943px;width:68px;height:22px;border-radius:11px;background:var(--accent);color:var(--white);font-size:7.5px;text-align:center;line-height:22px;letter-spacing:.5px}
.divider{left:461px;top:540px;width:1px;height:430px;background:#ececec}

/* contact list */
.info{left:507px;display:flex;gap:9px}
.info .ic{width:23px;height:23px;border-radius:50%;border:1px solid #999;display:flex;align-items:center;justify-content:center;margin-top:4px}
.info h4{font-size:10.5px;color:var(--accent);font-weight:700}
.info p{font-size:10.3px;color:var(--text);margin-top:1px}

/* footer */
.footer{left:0;top:997px;width:899px;height:171px;background:var(--footer)}
.footer-base{left:0;top:1168px;width:899px;height:32px;background:var(--footer-deep);color:#ccc;font-size:8px;text-align:center;line-height:32px}
.f-title{font-size:8px;letter-spacing:1px;color:var(--white);padding-bottom:8px;border-bottom:1px dotted #555}
.f-links{list-style:none;font-size:8.6px;color:var(--white)}
.f-links li{height:19.6px;padding-left:7px;position:relative}
.f-links li::before{content:"›";position:absolute;left:0;color:#666}
.f-input{background:var(--white);border-radius:2px;font-size:7px;color:#555;padding:3px 4px}
.f-sep{width:1px;background:#2a2a2a;top:1040px;height:110px}
.f-row{left:458px;width:152px;font-size:8.8px;color:var(--white);display:flex;align-items:center;gap:7px;padding-bottom:7px;border-bottom:1px solid #2e2e2e;white-space:nowrap}
.f-row svg{flex-shrink:0}
.f-brand{left:650px;top:1090px;width:155px;text-align:center;color:#bdbdbd;font-weight:600;font-size:12.5px;white-space:nowrap}
.f-brand .dot{display:inline-block;width:11px;height:11px;border-radius:50%;background:#bdbdbd;vertical-align:-1px;margin-right:5px}
.abn{left:650px;top:1137px;width:155px;text-align:center;color:var(--white);font-size:8.8px}
</style>
</head>
<body>

<div class="abs hero" role="img" aria-label="Photo of a desk with a plant, keyboard, pencil, notepad and a cup of coffee"></div>
<div class="abs topbar"></div>
<div class="abs brand"><span class="dot"></span>Tallow Ridge Energy</div>
<div class="abs phone-top">
  <svg width="20" height="20" viewBox="0 0 20 20"><circle cx="10" cy="10" r="9" fill="none" stroke="#fff" stroke-width="1.3"/><path d="M7 5.5l1.6 2.6-1 1c.6 1.3 1.5 2.2 2.8 2.8l1-1 2.6 1.6-.8 1.6c-3.8-.3-6.6-3.1-7-7z" fill="#fff"/></svg>
  1800 7 BIRCH
</div>
<div class="abs quote-btn">FREE QUOTE
  <svg class="abs" style="right:10px;top:3px" width="15" height="16" viewBox="0 0 15 16"><rect x="2" y="1" width="10" height="13" rx="1" fill="none" stroke="#fff" stroke-width="1.2"/><path d="M4.5 5h5M4.5 8h5M4.5 11h3" stroke="#fff" stroke-width="1"/></svg>
</div>
<nav class="abs nav display">
  <span>Home</span><span>About Us</span><span>Commercial</span><span>Residential</span><span>Products</span><span class="active">Contact</span>
</nav>

<div class="abs page-heading">
  <span class="rule"></span>
  <h1 class="page-title display">Contact</h1>
  <span class="rule"></span>
</div>
<p class="abs intro">We're here to help. Use the form or contact us on the details below and we'll be happy to answer any questions you may have.</p>

<h2 class="abs form-title display">Request Your Free Quote</h2>
<span class="abs label" style="left:130px;top:515px">First / Contact Name *</span>
<span class="abs label" style="left:276px;top:515px">Last / Company Name *</span>
<div class="abs field" style="left:130px;top:532px;width:137px;height:28px"></div>
<div class="abs field" style="left:276px;top:532px;width:138px;height:28px"></div>
<span class="abs label" style="left:130px;top:568px">Email Address *</span>
<div class="abs field" style="left:130px;top:585px;width:284px;height:28px"></div>
<span class="abs label" style="left:130px;top:621px">Phone Number *</span>
<div class="abs field" style="left:130px;top:638px;width:284px;height:28px"></div>
<span class="abs label" style="left:130px;top:675px">Street Address *</span>
<div class="abs field" style="left:130px;top:691px;width:284px;height:28px"></div>
<span class="abs label" style="left:130px;top:732px">Town / Suburb *</span>
<span class="abs label" style="left:251px;top:732px">State *</span>
<span class="abs label" style="left:344px;top:732px">Postcode *</span>
<div class="abs field" style="left:130px;top:748px;width:111px;height:28px"></div>
<div class="abs field select" style="left:251px;top:748px;width:82px;height:28px;font-size:8px">VIC
  <svg width="9" height="6" viewBox="0 0 9 6"><path d="M1 1l3.5 3.5L8 1" fill="none" stroke="#333" stroke-width="1.1"/></svg>
</div>
<div class="abs field" style="left:342px;top:748px;width:72px;height:28px"></div>
<span class="abs label" style="left:130px;top:788px">I am interested in *</span>
<div class="abs field select" style="left:130px;top:804px;width:284px;height:28px">Commercial Solar
  <svg width="9" height="6" viewBox="0 0 9 6"><path d="M1 1l3.5 3.5L8 1" fill="none" stroke="#333" stroke-width="1.1"/></svg>
</div>
<span class="abs label" style="left:130px;top:848px">Your message</span>
<div class="abs field" style="left:130px;top:864px;width:284px;height:63px"></div>
<div class="abs submit display">Submit</div>

<div class="abs divider"></div>

<div class="abs info" style="top:518px">
  <span class="ic"><svg width="11" height="11" viewBox="0 0 12 12"><path d="M2 1l2.2 3-1.2 1.2c.8 1.6 1.9 2.7 3.5 3.5L7.7 7.5 11 9.6 10 11.5C5.3 11 1 6.7.6 2z" fill="var(--accent)"/></svg></span>
  <div><h4>PHONE</h4><p>1800 7 BIRCH</p></div>
</div>
<div class="abs info" style="top:575px">
  <span class="ic"><svg width="11" height="8" viewBox="0 0 11 8"><rect width="11" height="8" rx="1" fill="var(--accent)"/><path d="M0.5 0.8l5 3.6 5-3.6" fill="none" stroke="#fff" stroke-width="0.9"/></svg></span>
  <div><h4>EMAIL</h4><p>enquiries@tallowridgeenergy.com.au</p></div>
</div>
<div class="abs info" style="top:632px">
  <span class="ic"><svg width="13" height="13" viewBox="0 0 14 14"><g fill="none" stroke="var(--accent)" stroke-width="1.1"><circle cx="7" cy="7" r="6"/><ellipse cx="7" cy="7" rx="2.6" ry="6"/><path d="M1 7h12M2 4h10M2 10h10"/></g></svg></span>
  <div><h4>WEBSITE</h4><p>www.tallowridgeenergy.com.au</p></div>
</div>
<div class="abs info" style="top:689px">
  <span class="ic"><svg width="10" height="13" viewBox="0 0 10 13"><path d="M5 0.5a4.3 4.3 0 00-4.3 4.3C.7 8 5 12.5 5 12.5S9.3 8 9.3 4.8A4.3 4.3 0 005 .5z" fill="var(--accent)"/><circle cx="5" cy="4.8" r="1.6" fill="#fff"/></svg></span>
  <div><h4>TALLOW RIDGE ENERGY</h4><p>Kellerton, Victoria</p></div>
</div>

<footer>
  <div class="abs footer"></div>

  <div class="abs" style="left:124px;top:1021px;width:82px"><div class="f-title display">Quick Links</div></div>
  <ul class="abs f-links" style="left:124px;top:1048px">
    <li>Home</li><li>About Us</li><li>Commercial</li><li>Residential</li><li>Products</li><li>Contact Us</li>
  </ul>
  <div class="abs f-sep" style="left:241px"></div>

  <div class="abs" style="left:275px;top:1021px;width:144px"><div class="f-title display">Quick Inquiry</div></div>
  <div class="abs f-input" style="left:275px;top:1048px;width:143px;height:15px">Name</div>
  <div class="abs f-input" style="left:275px;top:1068px;width:143px;height:14px">Email</div>
  <div class="abs f-input" style="left:275px;top:1087px;width:143px;height:47px">Message</div>
  <div class="abs submit display" style="left:275px;top:1139px;width:52px;height:17px;line-height:17px;font-size:6px">Submit</div>
  <div class="abs f-sep" style="left:436px"></div>

  <div class="abs" style="left:458px;top:1021px;width:152px"><div class="f-title display">Contact Details</div></div>
  <div class="abs f-row" style="top:1049px"><svg width="9" height="9" viewBox="0 0 12 12"><path d="M2 1l2.2 3-1.2 1.2c.8 1.6 1.9 2.7 3.5 3.5L7.7 7.5 11 9.6 10 11.5C5.3 11 1 6.7.6 2z" fill="var(--accent)"/></svg>1800 7 BIRCH</div>
  <div class="abs f-row" style="top:1075px;font-size:8px;gap:5px"><svg width="9" height="7" viewBox="0 0 11 8"><rect width="11" height="8" rx="1" fill="var(--accent)"/><path d="M0.5 0.8l5 3.6 5-3.6" fill="none" stroke="#161616" stroke-width="0.9"/></svg>enquiries@tallowridgeenergy.com.au</div>
  <div class="abs f-row" style="top:1101px"><svg width="9" height="9" viewBox="0 0 14 14"><g fill="none" stroke="var(--accent)" stroke-width="1.3"><circle cx="7" cy="7" r="6"/><path d="M1 7h12"/></g></svg>www.tallowridgeenergy.com.au</div>
  <div class="abs f-row" style="top:1127px;border:0;font-weight:700;font-size:9.6px"><svg width="8" height="10" viewBox="0 0 10 13"><path d="M5 .5a4.3 4.3 0 00-4.3 4.3C.7 8 5 12.5 5 12.5S9.3 8 9.3 4.8A4.3 4.3 0 005 .5z" fill="var(--accent)"/></svg>TALLOW RIDGE ENERGY</div>
  <div class="abs" style="left:473px;top:1142px;color:#fff;font-size:8.4px">Kellerton, Victoria</div>
  <div class="abs f-sep" style="left:641px"></div>

  <div class="abs f-brand"><span class="dot"></span>Tallow Ridge Energy</div>
  <div class="abs abn">ABN: 41 205 773 160</div>

  <div class="abs footer-base">Copyright © 2017 Tallow Ridge Energy. All Right Reserved.</div>
</footer>

</body>
</html>
```